Corporate Travel Technology Company needs new Business Card design

We need a new business card design to reflect our re-branded company. Our company is called tolvEn (pronounced tolvenn) and we provide Business Intelligence and mobile travel management solutions for the corporate travel industry. Our multinational customers use our solutions to manage large travel budgets and frequent travellers, as well as to save money and reduce risk. We'd like to see designs that use the blue and green palette as well as our corporate logo (attached below). The design should communicate innovation, insight, forward thinking, contemporary, trusted.

Target Market(s)

Large multinational corporates and Travel Agencies.

Industry/Entity Type

Business

Contact Information for Business Card

Rosalind Mercer
Chief Executive
tolvEn
Phone number - +61 (0)2 8134 2907
Email address - rosalind.mercer@tolven-example.com
Mobile number - +61 (0)438 516 702
www.tolven-example.com

Font styles to use
Other font styles liked:
• Please use font as close to corporate logo as possible

Colors
0255a3
0393ce
00a990
33b8a4
33a6d7
3176b5

Requirements
Must have
• Please include the words;
• Mobile Travel Management
• Accelerating Travel Business Insights
• Use corporate logo - although icon can be stylised if needed

```html
<!DOCTYPE html>
<html lang="en">
<head>
<meta charset="utf-8">
<title>tolvEn – Business Card</title>
<link href="https://fonts.googleapis.com/css2?family=Alegreya+Sans:wght@400;500;700&family=Crimson+Pro:wght@600&display=swap" rel="stylesheet">
<style>
  :root {
    --canvas-bg: #e6e8e8;
    --card-dark: #2a3838;
    --card-light: #f7f7f5;
    --brand-blue: #1aa3e0;
    --text-light: #ffffff;
    --text-muted: #dfe6e6;
    --logo-slate: #3d4c4f;
    --card-shadow: rgba(0, 0, 0, 0.22);
  }
  * { box-sizing: border-box; margin: 0; padding: 0; }
  html, body {
    width: 1200px;
    height: 950px;
    overflow: hidden;
    background: var(--canvas-bg);
  }
  .canvas {
    width: 1200px;
    height: 950px;
    display: flex;
    align-items: center;
    justify-content: center;
    gap: 48px;
  }
  .card {
    width: 530px;
    height: 320px;
    border-radius: 26px;
    box-shadow: 0 10px 28px var(--card-shadow);
    position: relative;
  }
  .card--front {
    background: var(--card-dark);
    display: flex;
    flex-direction: column;
    align-items: center;
    justify-content: center;
    text-align: center;
    color: var(--text-light);
    font-family: "Alegreya Sans", sans-serif;
  }
  .brand-mark {
    display: flex;
    align-items: center;
    gap: 10px;
    margin-bottom: 22px;
  }
  .brand-mark__dot {
    width: 22px;
    height: 22px;
    border-radius: 50%;
    background: var(--brand-blue);
  }
  .brand-mark__name {
    font-family: "Alegreya Sans", sans-serif;
    font-weight: 500;
    font-size: 34px;
    color: var(--brand-blue);
    letter-spacing: 0.5px;
  }
  .person__name {
    font-family: "Crimson Pro", serif;
    font-weight: 600;
    font-size: 27px;
    color: var(--brand-blue);
    line-height: 1.05;
  }
  .person__title {
    font-family: "Crimson Pro", serif;
    font-weight: 600;
    font-size: 21px;
    color: var(--text-light);
    margin-bottom: 16px;
  }
  .contact {
    font-size: 14.5px;
    color: var(--text-muted);
    line-height: 1.55;
  }
  .contact__sep { color: var(--brand-blue); padding: 0 4px; }
  .tagline {
    margin-top: 4px;
    font-size: 14.5px;
    color: var(--text-muted);
  }
  .tagline__bullet { color: var(--brand-blue); padding: 0 5px; }

  .card--back {
    background: var(--card-light);
    display: flex;
    align-items: center;
    justify-content: center;
  }
  .logo-lockup {
    display: flex;
    align-items: center;
    gap: 16px;
  }
  .logo-lockup__name {
    font-family: "Alegreya Sans", sans-serif;
    font-weight: 400;
    font-size: 86px;
    color: var(--logo-slate);
    letter-spacing: 1px;
  }
  .logo-lockup__dot {
    width: 36px;
    height: 36px;
    border-radius: 50%;
    background: var(--brand-blue);
  }
</style>
</head>
<body>
<main class="canvas">
  <section class="card card--front">
    <div class="brand-mark">
      <span class="brand-mark__dot"></span>
      <span class="brand-mark__name">tolvEn</span>
    </div>
    <h1 class="person__name">Rosalind Mercer</h1>
    <p class="person__title">Chief Executive</p>
    <p class="contact">+61 (0)2 8134 2907<span class="contact__sep">|</span>+61 (0)438 516 702<span class="contact__sep">|</span>www.tolven-example.com</p>
    <p class="contact">rosalind.mercer@tolven-example.com</p>
    <p class="tagline">Mobile Travel Management<span class="tagline__bullet">•</span>Accelerating Travel Business Insights</p>
  </section>

  <section class="card card--back">
    <div class="logo-lockup">
      <span class="logo-lockup__name">tolvEn</span>
      <span class="logo-lockup__dot"></span>
    </div>
  </section>
</main>
</body>
</html>
```